Phuket Thailand - Rental Villa Website

I have a villa for rent in Thailand and require a website - i need to demo pictures/walk through video, local attractions, villa facilities description plus seaonal rates and online booking.

Industry/Entity Type

Rental

Coding

Coded - Design and coding required

```html
<!DOCTYPE html>
<html lang="en">
<head>
<meta charset="utf-8">
<title>Palm Haven – Phuket Villa</title>
<link href="https://fonts.googleapis.com/css2?family=PT+Sans:wght@400;700&family=Open+Sans:wght@400;600&family=Bitter:wght@400;500&display=swap" rel="stylesheet">
<style>
:root{
  --dark:#232323;
  --footer:#2b2b2b;
  --blue:#1f5fa8;
  --red:#d8261c;
  --panel:#e9e9e9;
  --text:#333;
  --muted:#777;
  --white:#fff;
}
*{margin:0;padding:0;box-sizing:border-box}
html,body{width:735px;height:1200px;overflow:hidden;background:#fff}
body{position:relative;font-family:"PT Sans",sans-serif;color:var(--text)}
.abs{position:absolute}
.topbar{left:0;top:0;width:735px;height:45px;background:var(--dark)}
.brand{left:55px;top:11px;font-size:19px;color:var(--white);font-family:"PT Sans",sans-serif;font-weight:400}
.nav{top:17px;font-size:9px;color:#eee;letter-spacing:.3px}
.subbar{left:0;top:45px;width:735px;height:21px;background:#f5f5f5;border-bottom:1px solid #ddd}
.subbar .welcome{left:55px;top:5px;font-size:8.5px;color:var(--blue)}
.subbar .account{left:594px;top:5px;font-size:8.5px;color:var(--blue)}
.hero{left:0;top:66px;width:735px;height:296px;background:linear-gradient(180deg,#0d1a3a 0%,#1e2b4d 40%,#3a2c1e 70%,#2a2015 100%)}
.hero-title{left:0;top:188px;width:735px;text-align:center;font-family:"Open Sans",sans-serif;font-size:41px;color:var(--white)}
.arrow{top:196px;font-size:26px;color:rgba(255,255,255,.6)}
.rate{top:281px;width:144px;height:63px;background:rgba(215,215,215,.85);border:2px solid rgba(255,255,255,.5);border-radius:5px;text-align:center;font-family:"Bitter",serif}
.rate .label{margin-top:11px;font-size:15px;color:#222;letter-spacing:.5px}
.rate .price{font-size:17px;color:var(--red);font-weight:500}
.booking{left:0;top:362px;width:735px;height:199px;background:var(--panel)}
.pitch{left:60px;top:382px;width:225px;text-align:center}
.pitch h2{font-weight:400;font-size:11.5px;line-height:15px;color:#333}
.pitch h3{font-weight:400;font-size:11px;color:var(--blue);margin-top:6px}
.pitch p{font-size:7.3px;line-height:15px;color:var(--muted);margin-top:8px}
.field{width:156px;height:26px;background:var(--white);border-radius:7px;font-size:7px;color:#999;padding:9px 11px}
.cal{position:absolute;right:10px;top:8px}
.option{left:327px;top:514px;font-size:8px;color:var(--blue)}
.option .dot{display:inline-block;width:8px;height:8px;border-radius:50%;background:#ccc;margin-right:12px;vertical-align:middle}
.maplink{left:350px;top:530px;font-size:8px;color:var(--blue);text-decoration:underline}
.submit{left:568px;top:513px;width:96px;height:27px;background:var(--red);border-radius:8px;color:var(--white);font-family:"Bitter",serif;font-size:12.5px;letter-spacing:.8px;text-align:center;line-height:27px}
.section-title{font-family:"PT Sans",sans-serif;font-weight:400;font-size:16px;color:#222;letter-spacing:.3px}
.body-copy{font-size:7.3px;line-height:13px;color:var(--muted);text-align:justify}
.more{font-family:"Bitter",serif;font-size:10.5px;color:var(--blue)}
.photo-stack{left:460px;top:585px;width:222px;height:168px}
.frame{position:absolute;background:#fff;box-shadow:0 2px 5px rgba(0,0,0,.3)}
.tile{top:806px;width:151px;height:140px;box-shadow:0 1px 3px rgba(0,0,0,.3)}
.tile .tag{position:absolute;left:9px;top:87px;width:88px;height:44px;background:rgba(40,40,40,.75);color:#fff;font-size:9.5px;line-height:15px;text-align:center;padding-top:7px;letter-spacing:.3px}
.villa-shot{top:978px;width:151px;height:123px}
.footer{left:0;top:1132px;width:735px;height:68px;background:var(--footer)}
.footer .copy{left:55px;top:30px;font-size:6.8px;color:#ddd}
.social{top:30px;width:9px;height:9px;border-radius:50%;background:#eee}
</style>
</head>
<body>
<header>
  <div class="abs topbar"></div>
  <div class="abs brand">Palm Haven</div>
  <nav>
    <span class="abs nav" style="left:229px">Home</span>
    <span class="abs nav" style="left:285px">AboutUs</span>
    <span class="abs nav" style="left:353px">Destinations</span>
    <span class="abs nav" style="left:440px">Villa facilities</span>
    <span class="abs nav" style="left:532px">Seasonal Rates</span>
    <span class="abs nav" style="left:630px">Contact</span>
  </nav>
  <div class="abs subbar">
    <span class="abs welcome">Welcome to Phuket Thailand</span>
    <svg class="abs" style="left:574px;top:6px" width="8" height="9" viewBox="0 0 8 9"><circle cx="4" cy="2.3" r="2.2" fill="#1f5fa8"/><path d="M0 9c0-3 1.8-4.2 4-4.2S8 6 8 9z" fill="#1f5fa8"/></svg>
    <span class="abs account">My Accout</span>
    <svg class="abs" style="left:657px;top:6px" width="10" height="10" viewBox="0 0 10 10"><circle cx="4" cy="4" r="3" fill="none" stroke="#ccc" stroke-width="1.3"/><path d="M6.3 6.3L9.3 9.3" stroke="#ccc" stroke-width="1.5"/></svg>
  </div>
</header>

<section>
  <div class="abs hero" role="img" aria-label="Modern villa lit up at dusk with wooden deck and mountains behind"></div>
  <h1 class="abs hero-title" style="font-weight:400">Welcome to Palm Haven</h1>
  <span class="abs arrow" style="left:42px">&#10094;</span>
  <span class="abs arrow" style="left:679px">&#10095;</span>
  <div class="abs rate" style="left:87px"><div class="label">OFF SEASON</div><div class="price">$40.00</div></div>
  <div class="abs rate" style="left:296px"><div class="label">ON SEASON</div><div class="price">$48.00</div></div>
  <div class="abs rate" style="left:506px"><div class="label">SPECIAL OFFERS</div><div class="price">$35.00</div></div>
</section>

<section>
  <div class="abs booking"></div>
  <div class="abs pitch">
    <h2>1 MILLION HOLIDAY HOME LISTINGS,<br>1 WAY TO BOOK YOURS</h2>
    <h3>Book the vacation of your dream Holiday Villa!!</h3>
    <p>Et harum quidem rerum facilis est et expedita distinctio. Nam libero tempore, cum soluta nobis est eligendi optio cumque nihil impedit quo minus id quod maxime placeat facere possimus.</p>
  </div>
  <div class="abs field" style="left:326px;top:384px">First Name....</div>
  <div class="abs field" style="left:509px;top:384px">Last Name....</div>
  <div class="abs field" style="left:326px;top:428px">Phone....</div>
  <div class="abs field" style="left:509px;top:428px">Email....</div>
  <div class="abs field" style="left:326px;top:472px">Check In Date
    <svg class="cal" width="8" height="8" viewBox="0 0 8 8"><rect x=".5" y="1" width="7" height="6.5" fill="none" stroke="#bbb"/><path d="M.5 3h7" stroke="#bbb"/></svg></div>
  <div class="abs field" style="left:509px;top:472px">Check Out Date
    <svg class="cal" width="8" height="8" viewBox="0 0 8 8"><rect x=".5" y="1" width="7" height="6.5" fill="none" stroke="#bbb"/><path d="M.5 3h7" stroke="#bbb"/></svg></div>
  <div class="abs option"><span class="dot"></span>I do not have specific dates</div>
  <div class="abs maplink">Map View</div>
  <div class="abs submit">SUBMIT</div>
</section>

<section>
  <h2 class="abs section-title" style="left:55px;top:585px">Some Words About Us!</h2>
  <div class="abs body-copy" style="left:55px;top:617px;width:380px">
    <p>At vero eos et accusamus et iusto odio dignissimos ducimus qui blanditiis praesentium voluptatum deleniti atque corrupti quos dolores et quas molestias excepturi sint occaecati cupiditate non provident, similique sunt in culpa qui officia deserunt mollitia animi, id est laborum et dolorum fuga. Et harum quidem rerum facilis est et expedita distinctio.</p>
    <p style="margin-top:13px">At vero eos et accusamus et iusto odio dignissimos ducimus qui blanditiis praesentium voluptatum deleniti atque corrupti quos dolores et quas molestias excepturi sint occaecati cupiditate non provident.</p>
  </div>
  <div class="abs more" style="left:55px;top:726px">Read More &nbsp;&nbsp;&#9758;</div>
  <div class="abs photo-stack">
    <div class="frame" style="left:6px;top:10px;width:206px;height:146px;transform:rotate(-6deg)"></div>
    <div class="frame" style="left:14px;top:4px;width:206px;height:146px;transform:rotate(4deg)"></div>
    <div class="frame" style="left:12px;top:16px;width:200px;height:132px;padding:4px">
      <div style="width:100%;height:100%;background:linear-gradient(180deg,#8db4c9 0%,#5e7a6a 35%,#3fb6c0 65%,#2a8f9a 100%)" role="img" aria-label="Walk-through video still of a long-tail boat in a turquoise bay"></div>
      <svg style="position:absolute;left:4px;bottom:4px" width="192" height="14" viewBox="0 0 192 14"><rect width="192" height="14" fill="#1a1a1a" opacity=".85"/><rect x="4" y="3" width="20" height="8" rx="2" fill="#333"/><path d="M11 4.5l5 2.5-5 2.5z" fill="#fff"/><rect x="30" y="6" width="120" height="2" fill="#555"/><rect x="30" y="6" width="52" height="2" fill="#3aa0e0"/></svg>
      <svg style="position:absolute;left:90px;top:58px" width="20" height="20" viewBox="0 0 20 20"><circle cx="10" cy="10" r="9" fill="rgba(0,0,0,.4)"/><path d="M8 6l6 4-6 4z" fill="#fff"/></svg>
    </div>
  </div>
</section>

<section>
  <h2 class="abs section-title" style="left:0;top:773px;width:735px;text-align:center">Local Attractions</h2>
  <div class="abs tile" style="left:54px;background:linear-gradient(180deg,#4a56a8,#2c2f5a 60%,#1a1a2a)" role="img" aria-label="Bhumibol Bridge lit at night"><div class="tag">BHUMIBOL<br>BRIDGE</div></div>
  <div class="abs tile" style="left:213px;background:linear-gradient(180deg,#2a3a6a,#1a2040 60%,#3a3020)" role="img" aria-label="Democracy Monument at night"><div class="tag">DEMOCRACY<br>MONUMENT</div></div>
  <div class="abs tile" style="left:372px;background:linear-gradient(180deg,#b03fa8,#e04a6a 55%,#6a1a3a)" role="img" aria-label="Wat Arun temple at sunset"><div class="tag">WAT ARUN<br>TEMPLE</div></div>
  <div class="abs tile" style="left:531px;background:linear-gradient(180deg,#d89030,#e8a030 40%,#3a2410 75%,#c07a20)" role="img" aria-label="Sunset over Phuket beach with boats"><div class="tag">PHUKET BEACH<br>SUNSET</div></div>
</section>

<section>
  <div class="abs villa-shot" style="left:54px;background:linear-gradient(180deg,#5a4a40,#8a7a6a 55%,#c8c4bc)" role="img" aria-label="Villa bedroom interior"></div>
  <div class="abs villa-shot" style="left:213px;background:linear-gradient(160deg,#6a8a5a,#5a5a60 45%,#7a6a6a)" role="img" aria-label="Villa exterior with tiled roof and garden"></div>
  <h2 class="abs section-title" style="left:388px;top:976px">Villa Description</h2>
  <p class="abs body-copy" style="left:388px;top:1003px;width:287px;line-height:14px">At vero eos et accusamus et iusto odio dignissimos ducimus qui blanditiis praesentium voluptatum deleniti atque corrupti quos dolores et quas molestias excepturi sint occaecati cupiditate non provident, similique sunt in culpa qui officia deserunt mollitia animi, id est laborum et dolorum fuga. Et harum quidem rerum facilis est et expedita distinctio.</p>
  <div class="abs more" style="left:388px;top:1088px">Read Full Description &nbsp;&nbsp;&#9758;</div>
</section>

<footer>
  <div class="abs footer">
    <span class="abs copy">© Copyright Palm Haven Thailand. All rights reserved.</span>
    <span class="abs social" style="left:612px"></span>
    <span class="abs social" style="left:631px"></span>
    <span class="abs social" style="left:650px"></span>
    <span class="abs social" style="left:669px"></span>
  </div>
</footer>
</body>
</html>
```